Veltrano.co - Polar Expeditions Specialists

We need a modern, visually striking business card for Veltrano.co, a company specialized in selling expedition cruises to the most remote regions on Earth, with a focus on the Arctic and Antarctica. The design should instantly communicate that the cardholder is an expert in polar travel. Use clean, premium aesthetics with cool tones like icy blue and white, possibly incorporating polar imagery (ice, glaciers, penguins, etc.)

Attached the logo

Contact Information for Business Card

Feels high-end and trustworthy.. Visually memorable — encourages people to keep it

Colors
0054AA
0677BA
7BADD7
CADEEF
E8F1F8

Requirements
Must have
• ice, glaciers, penguins, montains
Nice to have
• modern, transparente,

```html
<!DOCTYPE html>
<html lang="en">
<head>
<meta charset="UTF-8">
<title>Veltrano.co – Business Card</title>
<link href="https://fonts.googleapis.com/css2?family=Poppins:wght@400;500;600;700&display=swap" rel="stylesheet">
<style>
  :root {
    --stage: #1d1d20;
    --brand-blue: #3272b0;
    --night: #11112a;
    --ice: #ffffff;
    --ice-soft: #e8f1f8;
    --ice-mid: #7badd7;
  }
  * { margin: 0; padding: 0; box-sizing: border-box; }
  html, body {
    width: 1200px; height: 900px; overflow: hidden;
    background: var(--stage);
    font-family: "Poppins", sans-serif;
  }
  .canvas { position: relative; width: 1200px; height: 900px; }
  .card {
    position: absolute; left: 230px; width: 740px; height: 410px;
    border-radius: 26px; overflow: hidden;
  }
  .card--front {
    top: 30px; background: var(--brand-blue);
    display: flex; flex-direction: column; align-items: center; justify-content: center;
    color: var(--ice);
  }
  .brand-mark {
    width: 96px; height: 96px; border-radius: 50%;
    background: var(--ice); margin-bottom: 18px;
  }
  .brand-name {
    font-weight: 700; font-size: 80px; line-height: 1; letter-spacing: 1px;
  }
  .brand-tagline {
    margin-top: 12px; font-weight: 600; font-size: 22px; letter-spacing: 0.5px;
  }
  .card--back { top: 460px; background: var(--night); }
  .polar-scene { position: absolute; inset: 0; width: 100%; height: 100%; }
  .contact { position: absolute; left: 48px; top: 86px; color: var(--ice); }
  .contact__accent {
    position: absolute; left: -48px; top: 4px; width: 10px; height: 46px;
    background: var(--brand-blue);
  }
  .contact__name {
    font-weight: 700; font-size: 30px; line-height: 1.1; color: var(--brand-blue);
  }
  .contact__role { font-weight: 400; font-size: 17px; margin-top: 2px; }
  .contact__address { font-size: 16px; line-height: 1.45; margin-top: 20px; }
  .contact__list { list-style: none; margin-top: 14px; font-size: 16px; line-height: 1.5; }
  .contact__list li { display: flex; align-items: center; gap: 10px; }
  .contact__icon { width: 13px; height: 13px; fill: var(--brand-blue); flex: none; }
</style>
</head>
<body>
<main class="canvas">
  <section class="card card--front">
    <span class="brand-mark" aria-hidden="true"></span>
    <h1 class="brand-name">Veltrano.co</h1>
    <p class="brand-tagline">Polar Expeditions Specialists</p>
  </section>

  <section class="card card--back">
    <svg class="polar-scene" viewBox="0 0 740 410" role="img" aria-label="Illustration of a polar bear with penguins on ice under a starry polar sky, in icy blue and white">
      <defs>
        <linearGradient id="polarGradient" x1="0" y1="0.2" x2="1" y2="0.9">
          <stop offset="0" stop-color="#3272b0"/>
          <stop offset="0.55" stop-color="#3a7bbb"/>
          <stop offset="0.8" stop-color="#7badd7"/>
          <stop offset="1" stop-color="#e8f1f8"/>
        </linearGradient>
      </defs>
      <path d="M740 0 L590 0 C500 20 440 110 420 210 C405 290 402 360 398 410 L740 410 Z" fill="url(#polarGradient)"/>
    </svg>

    <div class="contact">
      <span class="contact__accent"></span>
      <h2 class="contact__name">Marlow Kessing</h2>
      <p class="contact__role">CEO &amp; Founder</p>
      <p class="contact__address">48 Harbor Crest Lane,<br>Fairmont, ME 04011 USA</p>
      <ul class="contact__list">
        <li><svg class="contact__icon" viewBox="0 0 16 16"><path d="M3 1h3l1.5 4-2 1.5a9 9 0 0 0 4 4l1.5-2 4 1.5v3a2 2 0 0 1-2 2A13 13 0 0 1 1 3a2 2 0 0 1 2-2z"/></svg>+1.555.014.782</li>
        <li><svg class="contact__icon" viewBox="0 0 16 16"><path d="M1 3h14v10H1z M1 3l7 6 7-6" stroke="#11112a" stroke-width="1.2"/></svg>hello@veltranomail.com</li>
        <li><svg class="contact__icon" viewBox="0 0 16 16"><circle cx="8" cy="8" r="7"/><path d="M1 8h14M8 1c-3 3-3 11 0 14M8 1c3 3 3 11 0 14" stroke="#11112a" stroke-width="1" fill="none"/></svg>www.veltranotravel.com</li>
      </ul>
    </div>
  </section>
</main>
</body>
</html>
```